We need a new design/function for our reusable Sandwich paper bag

1. We need a designer who can help us create a design and improve the functionality of our paper lunch bag (image attached) and create "a new design for our new sandwich paper bag".

We would like to see designs for people age +18 ( working men, collage). The sandwich paper bag design should have a zipper (colored zipper is available) at the top, the sandwich bag dimension will be 8.5 x7.75x 1.5 in

2. The designer must also design a simple package cover for the sandwich bag

The feature of the material that will be used in manufacturing the sandwich paper bag: It combines the advantages of paper, film, and weaving. It is thinner than paper, but it is tough and tear resistant, texture and touch. Unique, waterproof, anti-fouling and weather-resistant, environmentally friendly and recyclable, has been widely used in textile

Target Market(s)

USA, Canada

Colors

Designer to choose colors to be used in the design.

Requirements
Must have
• Design for the sandwich paper bag
• Package design for the sandwich bag
• The designer must remember that there should be a zipper at the top of the bag
• Kindly find a suitable and small place to put our logo in it, besides the bag
Nice to have
• Try to design something that covers the crumpled paper bag look or appear it in a fashion way
• We appreciate if we can see an improvement in the functionality of the paper sandwich bag, not only the design. We need a new idea on how people will use this bag
Should not have
• Please don't use food images in your design

```html
<!DOCTYPE html>
<html lang="en">
<head>
<meta charset="utf-8">
<title>Eat. Travel. Repeat. – Sandwich Bag &amp; Wrap</title>
<link rel="stylesheet" href="https://fonts.googleapis.com/css2?family=Open+Sans:wght@400;700;800&display=swap">
<style>
  :root{
    --page:#eeeeee;
    --kraft:#e9b981;
    --kraft-dark:#d9a66d;
    --zipper:#f5c518;
    --ink:#2a3d57;
    --coral:#e05252;
    --coral-deep:#c94444;
    --navy:#2c4260;
    --navy-deep:#22344d;
    --steel:#7ea2ba;
    --cream:#f2eee8;
    --body:#2b2b2b;
  }
  *{box-sizing:border-box;margin:0;padding:0}
  html,body{width:1200px;height:1016px;overflow:hidden;background:var(--page)}
  body{position:relative;font-family:"Open Sans",Arial,sans-serif;color:var(--ink)}

  .theme-women{--accent:var(--coral);--accent-deep:var(--coral-deep);--headline:var(--cream);--dots:rgba(255,255,255,.35)}
  .theme-men{--accent:var(--navy);--accent-deep:var(--navy-deep);--headline:var(--steel);--dots:rgba(110,150,175,.55)}

  /* ---------- Bag front ---------- */
  .bag{position:absolute;top:60px;width:485px;height:420px;background:var(--kraft)}
  .bag--women{left:60px}
  .bag--men{left:645px}
  .bag__zipper{position:absolute;left:8px;top:-20px;width:470px;height:20px;background:var(--zipper);border-radius:6px 6px 0 0}
  .bag__zipper-pull{position:absolute;right:-28px;top:-4px;width:40px;height:8px;background:var(--zipper);border-radius:4px}
  .bag__art{position:absolute;inset:0}
  .bag__dots{position:absolute;background:var(--dots);border-radius:6px}
  .bag__dots--left{left:0;top:0;width:110px;height:418px;opacity:.55}
  .bag__dots--right{left:370px;top:150px;width:112px;height:180px;opacity:.6}
  .headline{position:absolute;left:147px;font-weight:800;color:var(--headline);line-height:1;white-space:nowrap}
  .headline--eat{top:101px;font-size:90px;letter-spacing:-4px}
  .headline--travel{top:183px;font-size:47px;letter-spacing:-1.5px}
  .headline--repeat{top:223px;font-size:47px;letter-spacing:-1.5px}
  .bag__emblem{position:absolute;left:159px;top:268px;width:121px;height:129px;background:var(--accent-deep);opacity:.55;border-radius:50% 50% 12px 12px}
  .bag__rule{position:absolute;left:269px;top:391px;width:215px;height:3px;background:var(--accent-deep)}
  .theme-men .bag__rule{background:var(--steel)}
  .bag__tag{position:absolute;left:485px;top:197px;width:23px;height:80px;background:var(--accent);display:flex;align-items:center;justify-content:center}
  .bag__tag span{writing-mode:vertical-rl;transform:rotate(180deg);color:#fff;font-size:9px;letter-spacing:.5px;white-space:nowrap}

  .caption{position:absolute;top:496px;width:485px;text-align:center;font-weight:700;font-size:12.5px;color:var(--ink)}
  .caption--women{left:60px}
  .caption--men{left:645px}

  /* ---------- Wrap ---------- */
  .wrap{position:absolute;left:59px;width:1076px;height:226px;background:var(--kraft)}
  .wrap--women{top:520px}
  .wrap--men{top:770px}
  .wrap__fold{position:absolute;left:537px;top:0;width:1px;height:100%;background:#1a1a1a}
  .wrap__band{position:absolute;left:0;bottom:0;width:100%;height:31px;background:var(--accent)}
  .wrap__dots{position:absolute;left:0;top:0;width:90px;height:110px;background:var(--dots);opacity:.45;border-radius:6px}
  .wrap__icon{position:absolute;left:250px;top:14px;width:32px;height:32px;background:var(--accent);opacity:.7;border-radius:50% 50% 6px 6px}
  .brand{position:absolute;left:176px;top:55px;width:186px;text-align:center;color:var(--accent);font-weight:800;line-height:1}
  .brand__line1{font-size:37px;letter-spacing:.5px}
  .brand__line2{display:flex;align-items:center;justify-content:space-between;font-size:37px;margin-top:-6px}
  .brand__dash{width:30px;height:4px;background:var(--accent)}
  .wrap__flourish{position:absolute;left:216px;top:131px;width:104px;height:7px;background:var(--accent);opacity:.45;border-radius:4px}
  .wrap__scene{position:absolute;left:106px;top:154px;width:325px;height:41px;background:linear-gradient(to bottom,rgba(255,255,255,0),var(--accent));opacity:.8}
  .slogan{position:absolute;left:106px;bottom:6px;width:325px;text-align:center;color:#fff;font-weight:800;font-size:14.5px;letter-spacing:.3px}

  .notes{position:absolute;left:589px;top:33px;width:436px}
  .notes__title{font-weight:800;font-size:9px;color:var(--accent);letter-spacing:.2px}
  .notes__divider{width:62px;height:6px;margin:4px 0 6px;background:var(--ink);opacity:.6;border-radius:3px}
  .notes__text{font-size:8px;line-height:12.6px;color:var(--body);margin-bottom:13px}
  .theme-men .notes__title{color:var(--ink)}

  .label-wrap{position:absolute;left:0;top:752px;width:1200px;text-align:center;font-weight:700;font-size:12.5px;color:var(--ink)}
</style>
</head>
<body>

  <!-- Bag front: women -->
  <section class="bag bag--women theme-women">
    <div class="bag__zipper"><div class="bag__zipper-pull"></div></div>
    <div class="bag__dots bag__dots--left" role="img" aria-label="Halftone dot pattern"></div>
    <div class="bag__dots bag__dots--right" role="img" aria-label="Halftone dot pattern"></div>
    <svg class="bag__art" viewBox="0 0 485 420" aria-hidden="true">
      <polygon points="147,112 317,112 337,175 297,329 484,329 484,418 0,418 0,274" fill="var(--accent)"/>
    </svg>
    <div class="bag__emblem" role="img" aria-label="Burger with city skyline emblem"></div>
    <div class="bag__rule"></div>
    <div class="headline headline--eat">EAT.</div>
    <div class="headline headline--travel">TRAVEL.</div>
    <div class="headline headline--repeat">REPEAT.</div>
    <div class="bag__tag"><span>COMPANY NAME</span></div>
  </section>
  <p class="caption caption--women">COLOR THAT SUITES WOMEN</p>

  <!-- Bag front: men -->
  <section class="bag bag--men theme-men">
    <div class="bag__zipper"><div class="bag__zipper-pull"></div></div>
    <div class="bag__dots bag__dots--left" role="img" aria-label="Halftone dot pattern"></div>
    <div class="bag__dots bag__dots--right" role="img" aria-label="Halftone dot pattern"></div>
    <svg class="bag__art" viewBox="0 0 485 420" aria-hidden="true">
      <polygon points="147,112 317,112 337,175 297,329 484,329 484,418 0,418 0,274" fill="var(--accent)"/>
    </svg>
    <div class="bag__emblem" role="img" aria-label="Burger with city skyline emblem"></div>
    <div class="bag__rule"></div>
    <div class="headline headline--eat">EAT.</div>
    <div class="headline headline--travel">TRAVEL.</div>
    <div class="headline headline--repeat">REPEAT.</div>
    <div class="bag__tag"><span>COMPANY NAME</span></div>
  </section>
  <p class="caption caption--men">COLOR THAT SUITES MEN</p>

  <!-- Wrap: women -->
  <section class="wrap wrap--women theme-women">
    <div class="wrap__dots" role="img" aria-label="Halftone dot pattern"></div>
    <div class="wrap__icon" role="img" aria-label="Burger icon"></div>
    <div class="brand">
      <div class="brand__line1">COMPANY</div>
      <div class="brand__line2"><span class="brand__dash"></span>NAME<span class="brand__dash"></span></div>
    </div>
    <div class="wrap__flourish" role="img" aria-label="Decorative flourish"></div>
    <div class="wrap__scene" role="img" aria-label="City skyline illustration"></div>
    <div class="wrap__band"></div>
    <p class="slogan">YOUR SLOGAN GOES HERE</p>
    <div class="wrap__fold"></div>
    <div class="notes">
      <h3 class="notes__title">INSTRUCTION</h3>
      <div class="notes__divider" role="img" aria-label="Decorative divider"></div>
      <p class="notes__text">Lorem Ipsum is simply dummy text of the printing and typesetting industry. Lorem Ipsum has been the industry's standard dummy text ever since the 1500s, when an unknown printer took a galley of type and scrambled it to make a type specimen book.</p>
      <h3 class="notes__title">PRECAUTION</h3>
      <div class="notes__divider" role="img" aria-label="Decorative divider"></div>
      <p class="notes__text">Lorem Ipsum is simply dummy text of the printing and typesetting industry. Lorem Ipsum has been the industry's standard dummy text ever since the 1500s, when an unknown printer took a galley of type and scrambled it to make a type specimen book.</p>
    </div>
  </section>

  <p class="label-wrap">WRAP</p>

  <!-- Wrap: men -->
  <section class="wrap wrap--men theme-men">
    <div class="wrap__dots" role="img" aria-label="Halftone dot pattern"></div>
    <div class="wrap__icon" role="img" aria-label="Burger icon"></div>
    <div class="brand">
      <div class="brand__line1">COMPANY</div>
      <div class="brand__line2"><span class="brand__dash"></span>NAME<span class="brand__dash"></span></div>
    </div>
    <div class="wrap__flourish" role="img" aria-label="Decorative flourish"></div>
    <div class="wrap__scene" role="img" aria-label="City skyline illustration"></div>
    <div class="wrap__band"></div>
    <p class="slogan">YOUR SLOGAN GOES HERE</p>
    <div class="wrap__fold"></div>
    <div class="notes">
      <h3 class="notes__title">INSTRUCTION</h3>
      <div class="notes__divider" role="img" aria-label="Decorative divider"></div>
      <p class="notes__text">Lorem Ipsum is simply dummy text of the printing and typesetting industry. Lorem Ipsum has been the industry's standard dummy text ever since the 1500s, when an unknown printer took a galley of type and scrambled it to make a type specimen book.</p>
      <h3 class="notes__title">PRECAUTION</h3>
      <div class="notes__divider" role="img" aria-label="Decorative divider"></div>
      <p class="notes__text">Lorem Ipsum is simply dummy text of the printing and typesetting industry. Lorem Ipsum has been the industry's standard dummy text ever since the 1500s, when an unknown printer took a galley of type and scrambled it to make a type specimen book.</p>
    </div>
  </section>

</body>
</html>
```